Investment company needing business card

We are wanting a business card which looks sharp and easy on the eye. We are thinking of having a business card with the logo embossed on it, to really make it stand out. We will only have a small amount of information of the business card, person's name, position, email address and phone number

Contact Information for Business Card

Danielle Frost
Executive Assistant
+64 21 473 5162
danielf@harwickpartners.co.nz

Requirements
Must have
• Embossed logo
Should not have
• Not to be busy

```html
<!DOCTYPE html>
<html lang="en">
<head>
<meta charset="utf-8">
<title>Harwick Partners – Business Card</title>
<link rel="stylesheet" href="https://fonts.googleapis.com/css2?family=Lato:wght@400;700;900&display=swap">
<style>
  :root {
    --canvas: #e9eaeb;
    --charcoal: #22272a;
    --green: #24b473;
    --grey: #5f6163;
    --cream: #ebe6dc;
    --white: #ffffff;
    --ink: #4a4c4e;
  }
  * { box-sizing: border-box; margin: 0; padding: 0; }
  html, body {
    width: 1200px; height: 800px; overflow: hidden;
    background: var(--canvas);
    font-family: "Lato", sans-serif;
  }
  .stage {
    width: 1200px; height: 800px;
    display: flex; align-items: center; justify-content: center; gap: 40px;
  }
  .card {
    position: relative;
    width: 540px; height: 309px;
    overflow: hidden;
    box-shadow: 0 10px 28px rgba(0,0,0,.18);
  }

  /* Front */
  .card-front { background: var(--charcoal); }
  .card-front .band-green {
    position: absolute; left: 0; bottom: 0;
    width: 58%; height: 16px; background: var(--green);
  }
  .card-front .band-cream {
    position: absolute; right: 0; bottom: 0;
    width: 42%; height: 8px; background: var(--cream);
  }
  .brand {
    display: flex; align-items: center; gap: 12px;
    color: var(--green);
    font-weight: 900; text-transform: uppercase;
  }
  .brand-mark { width: 30px; height: 30px; background: var(--green); flex: none; }
  .card-front .brand {
    position: absolute; left: 50%; top: 44%;
    transform: translate(-50%, -50%);
    font-size: 28px; letter-spacing: 2px; white-space: nowrap;
  }

  /* Back */
  .card-back { background: var(--green); }
  .card-back .sweep { position: absolute; inset: 0; }
  .card-back .brand {
    position: absolute; left: 34px; top: 112px;
    font-size: 24px; letter-spacing: 1.5px; white-space: nowrap;
  }
  .card-back .brand-mark { width: 26px; height: 26px; }
  .contact { position: absolute; left: 34px; bottom: 30px; color: var(--ink); }
  .contact-name { color: var(--green); font-weight: 700; font-size: 17px; line-height: 1.1; }
  .contact-role { font-size: 12.5px; margin-bottom: 12px; }
  .contact-line { display: flex; align-items: center; gap: 8px; font-size: 11.5px; line-height: 1.6; }
  .contact-line svg { width: 11px; height: 11px; flex: none; }
</style>
</head>
<body>
<main class="stage">
  <section class="card card-front">
    <div class="brand"><span class="brand-mark"></span>Harwick Partners</div>
    <div class="band-green"></div>
    <div class="band-cream"></div>
  </section>

  <section class="card card-back">
    <svg class="sweep" viewBox="0 0 540 309" preserveAspectRatio="none" aria-hidden="true">
      <path d="M220 0 H300 C420 40 475 120 495 205 C455 115 370 40 220 0 Z" fill="var(--grey)"/>
      <path d="M0 0 H270 C410 35 470 170 472 309 H0 Z" fill="var(--white)"/>
    </svg>
    <div class="brand"><span class="brand-mark"></span>Harwick Partners</div>
    <div class="contact">
      <p class="contact-name">Danielle Frost</p>
      <p class="contact-role">Executive Assistant</p>
      <p class="contact-line">
        <svg viewBox="0 0 12 12"><rect x="3" y="1" width="6" height="10" rx="1" fill="none" stroke="var(--green)" stroke-width="1.2"/></svg>
        +64 21 473 5162
      </p>
      <p class="contact-line">
        <svg viewBox="0 0 12 12"><rect x="1" y="2.5" width="10" height="7" fill="var(--green)"/><path d="M1 2.5 L6 6.5 L11 2.5" fill="none" stroke="var(--white)" stroke-width="1"/></svg>
        danielf@harwickpartners.co.nz
      </p>
    </div>
  </section>
</main>
</body>
</html>
```